Harborline Renewal Business Card Design

Professional and clean design. The design colors should flow with the logo. Two-sided card with the website on the back which is:

www.HarborlineRenewal.example.

"Specializing in Water Damage Restoration"

On the front I need the name, email, phone, and logo.

Name: Darnell Quisby
Email: Darnell@HarborlineRenewal.example
Phone: 555-318-2046 for now

I only have the Preview and Thumbnail right now but should have the source files uploaded within a day or two.

Target Market(s)

Flood victims, home owners with water damage from busted pipes etc...

Industry/Entity Type

Business

Contact Information for Business Card

Name: Darnell Quisby

Font styles to use
Serif
Sans Serif

Requirements
Must have
• Business Card Details Info

```html
<!DOCTYPE html>
<html lang="en">
<head>
<meta charset="utf-8">
<title>Harborline Renewal Business Card</title>
<link rel="stylesheet" href="https://fonts.googleapis.com/css2?family=Cinzel:wght@500&family=Open+Sans:wght@400&family=PT+Sans:wght@400;700&display=swap">
<style>
  :root {
    --page: #e8e5e1;
    --card: #eef1f3;
    --blue-deep: #1f6f9e;
    --blue-mid: #3a8fbf;
    --blue-light: #8cc3e0;
    --ink-brand: #1d5f8c;
    --ink-name: #3b7ea6;
    --ink-contact: #2f78a8;
  }
  * { margin: 0; padding: 0; box-sizing: border-box; }
  html, body { width: 1200px; height: 970px; overflow: hidden; }
  body { background: var(--page); position: relative; }

  .card {
    position: absolute; left: 100px; top: 193px;
    width: 1000px; height: 584px;
    background: linear-gradient(135deg, #f4f6f7 0%, var(--card) 55%, #e4ecf1 100%);
    box-shadow: 0 10px 30px rgba(0,0,0,.18);
    overflow: hidden;
  }
  .card-waves { position: absolute; inset: 0; width: 1000px; height: 584px; }

  .brand {
    position: absolute; right: 55px; top: 60px;
    width: 460px; text-align: center;
  }
  .brand-dot {
    width: 124px; height: 124px; border-radius: 50%;
    background: var(--ink-brand); margin: 0 auto 18px auto;
    position: relative; left: 18px;
  }
  .brand-name {
    font-family: "Cinzel", serif; font-weight: 500;
    color: var(--ink-brand); line-height: 1;
  }
  .brand-name .line-1 { display: block; font-size: 58px; letter-spacing: 2px; }
  .brand-name .line-2 { display: block; font-size: 25px; letter-spacing: 7px; margin-top: 6px; }
  .tagline {
    font-family: "Open Sans", sans-serif; font-size: 20px;
    color: var(--ink-brand); margin-top: 6px; white-space: nowrap;
  }

  .person {
    position: absolute; left: 42px; top: 318px;
    font-family: "PT Sans", sans-serif;
  }
  .person-name {
    font-weight: 700; font-size: 36px; color: var(--ink-name);
    margin-bottom: 46px;
  }
  .contact-list { list-style: none; }
  .contact-list li {
    display: flex; align-items: center; gap: 9px;
    font-size: 25px; color: var(--ink-contact);
    height: 35px; white-space: nowrap;
  }
  .contact-icon { width: 25px; height: 25px; flex: none; }
</style>
</head>
<body>
  <div class="card">
    <svg class="card-waves" viewBox="0 0 1000 584" aria-hidden="true">
      <defs>
        <linearGradient id="topWave" x1="0" y1="0" x2="1" y2="1">
          <stop offset="0" stop-color="#5aa6cf"/>
          <stop offset="1" stop-color="#2f86bb"/>
        </linearGradient>
        <linearGradient id="bottomWave" x1="0" y1="1" x2="1" y2="0">
          <stop offset="0" stop-color="#3b8fc0"/>
          <stop offset="1" stop-color="#1b6797"/>
        </linearGradient>
      </defs>
      <path d="M0,0 H1000 V14 C720,22 330,80 0,292 Z" fill="url(#topWave)"/>
      <path d="M0,584 V568 C600,574 850,470 1000,265 V584 Z" fill="url(#bottomWave)"/>
      <path d="M0,578 C620,582 870,490 1000,300" fill="none" stroke="#a9d2e8" stroke-width="2.5" opacity=".55"/>
    </svg>

    <div class="brand">
      <div class="brand-dot"></div>
      <div class="brand-name">
        <span class="line-1">HARBORLINE</span>
        <span class="line-2">RENEWAL</span>
      </div>
      <div class="tagline">Specializing in Water Damage Restoration</div>
    </div>

    <div class="person">
      <div class="person-name">Darnell Quisby</div>
      <ul class="contact-list">
        <li>
          <svg class="contact-icon" viewBox="0 0 26 26" aria-hidden="true">
            <rect width="26" height="26" rx="3" fill="var(--ink-contact)"/>
            <path d="M6,10 Q13,4 20,10 L18,12 L15,10 L11,10 L8,12 Z M8,13 H18 L19,20 H7 Z" fill="#eef1f3"/>
          </svg>
          555-318-2046
        </li>
        <li>
          <svg class="contact-icon" viewBox="0 0 26 26" aria-hidden="true">
            <rect width="26" height="26" rx="3" fill="var(--ink-contact)"/>
            <rect x="5" y="8" width="16" height="11" fill="none" stroke="#eef1f3" stroke-width="1.6"/>
            <path d="M5,8 L13,15 L21,8" fill="none" stroke="#eef1f3" stroke-width="1.6"/>
          </svg>
          Darnell@HarborlineRenewal.example
        </li>
        <li>
          <svg class="contact-icon" viewBox="0 0 26 26" aria-hidden="true">
            <rect width="26" height="26" rx="3" fill="var(--ink-contact)"/>
            <circle cx="13" cy="13" r="8" fill="none" stroke="#eef1f3" stroke-width="1.5"/>
            <ellipse cx="13" cy="13" rx="3.5" ry="8" fill="none" stroke="#eef1f3" stroke-width="1.2"/>
            <path d="M5,13 H21 M6.5,9 H19.5 M6.5,17 H19.5" stroke="#eef1f3" stroke-width="1.2"/>
          </svg>
          www.HarborlineRenewal.example
        </li>
      </ul>
    </div>
  </div>
</body>
</html>
```